Local Flower Farm Needs Business Card Design

I need business cards designed for a flower farm based in Eudora, Kansas.
Business Info:
We are a local cut flower farm located in Eudora, Kansas, founded by Corinne Haldwick. What started as a passion for agriculture and search for more joy in daily life has blossomed into a small business dedicated to providing the community with beautiful, fresh, and sustainable flowers. We specialize in local, seasonal blooms, ensuring that every petal reflects the care and dedication we pour into our craft. Our mission is to deliver the highest quality flowers directly to our customers through local farmers markets and to florists who share our commitment to sustainability. Join us in celebrating the beauty of nature, one bloom at a time!
Contact Details:
Corinne Haldwick
Owner
Phone 913-555-0147
Facebook: Rosalind Thorpe Gardens
Instagram: @RosalindThorpeGardens
Website: RosalindThorpeGardens.example
Target Market(s)
Wholesale to Florists and Direct to Consumer via Farmers Market
Industry/Entity Type
Florist, Farm
Contact Information for Business Card
Name, Contact Info, Logo
Look and feel
Each slider illustrates characteristics of the customer's brand and the style your logo design should communicate.

```html
<!DOCTYPE html>
<html lang="en">
<head>
<meta charset="utf-8">
<title>Rosalind Thorpe Gardens — Business Card</title>
<link rel="stylesheet" href="https://fonts.googleapis.com/css2?family=Libre+Baskerville&family=Outfit:wght@400&display=swap">
<style>
  :root {
    --ink: #0b2a30;
    --ink-soft: #123a41;
    --paper: #ffffff;
    --backdrop: #d9d9d9;
    --line: #1c3b40;
    --bloom: #e9ebec;
  }
  * { box-sizing: border-box; margin: 0; padding: 0; }
  html, body { width: 1200px; height: 1015px; overflow: hidden; }
  body { background: var(--backdrop); position: relative; font-family: "Outfit", sans-serif; }

  .card {
    position: absolute;
    width: 700px; height: 400px;
    overflow: hidden;
    box-shadow: 0 10px 28px rgba(0,0,0,.25);
  }

  /* Back side */
  .card--back { left: 110px; top: 80px; background: var(--ink); }
  .card--back .bloom-decor {
    position: absolute; right: 40px; top: 30px; width: 260px; height: 340px;
    background: radial-gradient(ellipse at center, rgba(255,255,255,.06), rgba(255,255,255,0) 70%);
  }
  .brand-seal {
    position: absolute; left: 50%; top: 50%; transform: translate(-50%, -50%);
    width: 200px; height: 200px; border-radius: 50%;
    display: flex; align-items: center; justify-content: center; text-align: center;
    font-family: "Libre Baskerville", serif; font-size: 17px; line-height: 1.45; letter-spacing: .06em;
  }
  .card--back .brand-seal { border: 1.5px solid rgba(255,255,255,.85); color: #fff; }

  /* Front side */
  .card--front { left: 390px; top: 530px; background: var(--paper); }
  .card--front .brand-seal {
    left: auto; top: 100px; right: 18px; transform: translateY(-50%);
    width: 160px; height: 160px; font-size: 14px; border: 1.2px solid var(--line); color: var(--ink);
  }
  .card--front .bloom-decor {
    position: absolute; right: 0; top: 150px; width: 150px; height: 170px;
    background: radial-gradient(ellipse at 70% 50%, var(--bloom), rgba(255,255,255,0) 70%);
  }
  .holder { position: absolute; left: 50px; top: 148px; color: var(--ink); }
  .holder__name { font-family: "Libre Baskerville", serif; font-size: 20px; letter-spacing: .03em; text-transform: uppercase; line-height: 1.2; }
  .holder__role { font-size: 16px; margin-top: 1px; }

  .orbit { position: absolute; left: 0; top: 0; }
  .panel {
    position: absolute; left: 100px; top: 215px;
    width: 460px; height: 460px; border-radius: 50%;
    background: var(--ink);
  }
  .contacts {
    position: absolute; left: 180px; top: 280px;
    list-style: none; color: #fff; font-size: 20px; line-height: 1;
  }
  .contacts li { display: flex; align-items: center; gap: 9px; margin-bottom: 10px; }
  .contacts .icon {
    width: 22px; height: 22px; border-radius: 50%; border: 1.3px solid #fff;
    display: flex; align-items: center; justify-content: center; flex: none;
  }
</style>
</head>
<body>

  <section class="card card--back" aria-label="Card back">
    <div class="bloom-decor" role="img" aria-label="Faint floral stem decoration"></div>
    <div class="brand-seal">Rosalind<br>Thorpe<br>Gardens</div>
  </section>

  <section class="card card--front" aria-label="Card front">
    <div class="bloom-decor" role="img" aria-label="Faint line-drawn flower decoration"></div>
    <div class="brand-seal">Rosalind<br>Thorpe<br>Gardens</div>

    <div class="holder">
      <p class="holder__name">Corinne Haldwick</p>
      <p class="holder__role">Owner</p>
    </div>

    <svg class="orbit" width="700" height="400" viewBox="0 0 700 400" aria-hidden="true">
      <path d="M 240 205 Q 375 165 510 235" fill="none" stroke="var(--line)" stroke-width="1.5"/>
      <circle cx="240" cy="205" r="3.5" fill="var(--line)"/>
      <circle cx="510" cy="235" r="3.5" fill="var(--line)"/>
    </svg>

    <div class="panel"></div>

    <ul class="contacts">
      <li>
        <span class="icon">
          <svg width="12" height="12" viewBox="0 0 24 24"><path d="M6.6 10.8a15 15 0 0 0 6.6 6.6l2.2-2.2c.3-.3.7-.4 1-.2 1.1.4 2.3.6 3.6.6.6 0 1 .4 1 1V20c0 .6-.4 1-1 1A17 17 0 0 1 3 4c0-.6.4-1 1-1h3.5c.6 0 1 .4 1 1 0 1.3.2 2.5.6 3.6.1.3 0 .7-.2 1z" fill="#fff"/></svg>
        </span>913-555-0147
      </li>
      <li><span class="icon"></span>Rosalind Thorpe Gardens</li>
      <li><span class="icon"></span>@RosalindThorpeGardens</li>
      <li>
        <span class="icon">
          <svg width="14" height="14" viewBox="0 0 24 24" fill="none" stroke="#fff" stroke-width="1.8"><circle cx="12" cy="12" r="9"/><path d="M3 12h18M12 3c3 3 3 15 0 18M12 3c-3 3-3 15 0 18"/></svg>
        </span>RosalindThorpeGardens.example
      </li>
    </ul>
  </section>

</body>
</html>
```